Business Card Design

New business card design

Target Market(s)

Residential & Commercial Property Managers

Industry/Entity Type

Plumbing Services

Contact Information for Business Card

Name - Rowan Keddle, title - Director, Phone Number - 0431 286 517, email - rowan@tbk-plumbing.com.au, Company ABN - 73 215 904 386,

Font styles to use
Sans Serif

Colors
0054AA
0677BA
7BADD7
CADEEF
E8F1F8

```html
<!DOCTYPE html>
<html lang="en">
<head>
<meta charset="utf-8">
<title>TBK Plumbing Services – Business Card</title>
<link href="https://fonts.googleapis.com/css2?family=Montserrat:wght@400;600;700&family=Roboto:wght@300;400&display=swap" rel="stylesheet">
<style>
  :root {
    --bg: #2a2a2a;
    --card-dark: #1b1c1e;
    --card-light: #f4f4f4;
    --ink: #111111;
    --muted: #8d8d8d;
    --grey-swoosh: #766f66;
    --blue: #1aa0e0;
    --white: #ffffff;
  }
  * { box-sizing: border-box; margin: 0; padding: 0; }
  html, body { width: 1200px; height: 852px; overflow: hidden; }
  body {
    background: var(--bg);
    display: flex;
    align-items: center;
    justify-content: center;
    gap: 40px;
    font-family: "Roboto", Arial, sans-serif;
  }
  .card {
    position: relative;
    width: 540px;
    height: 310px;
    border-radius: 18px;
    overflow: hidden;
    box-shadow: 0 0 0 2px var(--blue);
  }
  .card--back { background: var(--card-dark); }
  .card--front { background: var(--card-light); }

  .brand {
    position: absolute;
    display: flex;
    align-items: center;
    gap: 10px;
    font-family: "Montserrat", Arial, sans-serif;
    font-weight: 600;
    letter-spacing: 0.5px;
    white-space: nowrap;
  }
  .brand__dot {
    width: 14px; height: 14px;
    border-radius: 50%;
    background: var(--blue);
    flex: none;
  }
  .card--back .brand {
    left: 0; right: 0; top: 0; bottom: 0;
    justify-content: center;
    color: var(--white);
    font-size: 28px;
  }
  .card--front .brand {
    left: 34px; top: 104px;
    color: var(--ink);
    font-size: 20px;
  }

  .card__art { position: absolute; inset: 0; width: 100%; height: 100%; }

  .holder {
    position: absolute;
    right: 34px; top: 24px;
    text-align: right;
  }
  .holder__name {
    font-family: "Montserrat", Arial, sans-serif;
    font-weight: 700;
    font-size: 18px;
    color: var(--ink);
  }
  .holder__title {
    font-size: 12px;
    color: var(--muted);
    margin-top: 2px;
  }

  .contact {
    position: absolute;
    right: 18px; top: 160px;
    list-style: none;
    color: var(--white);
    font-size: 12px;
    font-weight: 300;
    text-align: right;
    white-space: nowrap;
  }
  .contact li {
    display: flex;
    justify-content: flex-end;
    align-items: center;
    gap: 8px;
    height: 18px;
  }
  .contact__icon { width: 11px; height: 11px; flex: none; }
  .contact__spacer { width: 11px; flex: none; }
</style>
</head>
<body>

  <section class="card card--back" aria-label="Card back">
    <div class="brand"><span class="brand__dot"></span>TBK Plumbing Services</div>
  </section>

  <section class="card card--front" aria-label="Card front">
    <svg class="card__art" viewBox="0 0 540 310" preserveAspectRatio="none" aria-hidden="true">
      <path class="wave-grey" d="M0,280 C150,278 240,258 296,198 C250,266 150,290 0,290 Z" fill="var(--grey-swoosh)"/>
      <path class="wave-dark" d="M0,294 C140,292 230,272 290,210 C345,150 420,104 540,98 L540,310 L0,310 Z" fill="var(--ink)"/>
      <path class="wave-blue" d="M130,276 C240,262 270,240 300,190 C350,120 430,80 540,76" fill="none" stroke="var(--blue)" stroke-width="4" stroke-linecap="round"/>
    </svg>

    <div class="brand"><span class="brand__dot"></span>TBK Plumbing Services</div>

    <div class="holder">
      <p class="holder__name">Rowan Keddle</p>
      <p class="holder__title">Director</p>
    </div>

    <ul class="contact">
      <li>0431 286 517
        <svg class="contact__icon" viewBox="0 0 12 12"><path d="M2.5 1 L4.5 1 L5.3 3.5 L4 4.6 C4.7 6 5.9 7.3 7.4 8 L8.5 6.7 L11 7.5 L11 9.5 C11 10.3 10.3 11 9.5 11 C5 11 1 7 1 2.5 C1 1.7 1.7 1 2.5 1 Z" fill="var(--blue)"/></svg>
      </li>
      <li>rowan@tbk-plumbing.com.au
        <svg class="contact__icon" viewBox="0 0 12 12"><rect x="0.5" y="2" width="11" height="8" fill="var(--blue)"/><path d="M0.5 2 L6 6.5 L11.5 2" fill="none" stroke="var(--ink)" stroke-width="1"/></svg>
      </li>
      <li>www.tbk-plumbing.com.au
        <svg class="contact__icon" viewBox="0 0 12 12"><circle cx="6" cy="6" r="5.2" fill="none" stroke="var(--blue)" stroke-width="1.2"/><ellipse cx="6" cy="6" rx="2.2" ry="5.2" fill="none" stroke="var(--blue)" stroke-width="1"/><line x1="0.8" y1="6" x2="11.2" y2="6" stroke="var(--blue)" stroke-width="1"/></svg>
      </li>
      <li>ABN 73 215 904 386<span class="contact__spacer"></span></li>
      <li>12 Harbour Lane, Eastwood NSW 2122<span class="contact__spacer"></span></li>
    </ul>
  </section>

</body>
</html>
```